business card deign

Logo needs the following on it.
1. attached logo
2. Tagline - "If it chills the cooler or lifts the crowd...count us in!"
3. Name- Dalton Pikes, Founder and CPO
4. Address - 412 E. Carver Avenue, Ste 2207, Tampa, FL. 33917
5. Phone - 555.318.4726

```html
<!DOCTYPE html>
<html lang="en">
<head>
<meta charset="utf-8">
<title>Coolrun business card</title>
<link href="https://fonts.googleapis.com/css2?family=Open+Sans:wght@400;700&family=Roboto:wght@700&display=swap" rel="stylesheet">
<style>
  :root {
    --backdrop: #232323;
    --card: #141414;
    --ink: #ffffff;
    --ink-soft: #e6e6e6;
  }
  * { box-sizing: border-box; margin: 0; padding: 0; }
  html, body {
    width: 1200px; height: 711px; overflow: hidden;
    background: var(--backdrop);
    font-family: "Open Sans", sans-serif;
    color: var(--ink);
  }
  .stage {
    width: 1200px; height: 711px;
    display: flex; align-items: center; justify-content: center; gap: 50px;
  }
  .card {
    position: relative;
    width: 525px; height: 300px;
    background: var(--card);
    border-radius: 24px;
    overflow: hidden;
  }
  .card-front { display: flex; align-items: center; justify-content: center; }
  .brand {
    display: flex; align-items: center; gap: 14px;
    font-family: "Open Sans", sans-serif;
    font-weight: 700;
    letter-spacing: 0.32em;
    text-transform: uppercase;
    color: var(--ink);
  }
  .brand-mark { background: var(--ink); flex: none; }
  .card-front .brand { font-size: 38px; }
  .card-front .brand-mark { width: 26px; height: 26px; }

  .card-back .brand { position: absolute; left: 34px; top: 95px; font-size: 24px; gap: 10px; }
  .card-back .brand-mark { width: 16px; height: 16px; }
  .holder {
    position: absolute; right: 34px; top: 26px;
    text-align: right;
  }
  .holder-name {
    font-family: "Roboto", sans-serif; font-weight: 700;
    font-size: 25px; line-height: 1.1;
  }
  .holder-role { font-size: 13px; margin-top: 2px; color: var(--ink-soft); }
  .accent-bar {
    position: absolute; right: 0; top: 24px;
    width: 18px; height: 50px; background: var(--ink);
  }
  .contact {
    position: absolute; right: 26px; top: 150px;
    list-style: none; text-align: right;
    font-size: 14px; line-height: 1.35; color: var(--ink-soft);
  }
  .contact li { display: flex; justify-content: flex-end; align-items: flex-start; gap: 8px; }
  .contact svg { width: 13px; height: 13px; flex: none; margin-top: 3px; fill: var(--ink); }
  .tagline {
    position: absolute; left: 34px; bottom: 26px;
    font-size: 14px; line-height: 1.35; color: var(--ink-soft);
    width: 230px;
  }
</style>
</head>
<body>
<main class="stage">
  <section class="card card-front" aria-label="Card front">
    <div class="brand"><span class="brand-mark"></span>Coolrun</div>
  </section>

  <section class="card card-back" aria-label="Card back">
    <div class="accent-bar"></div>
    <div class="holder">
      <p class="holder-name">Dalton Pikes</p>
      <p class="holder-role">Founder and CPO</p>
    </div>

    <div class="brand"><span class="brand-mark"></span>Coolrun</div>

    <ul class="contact">
      <li>555.318.4726
        <svg viewBox="0 0 24 24" aria-hidden="true"><path d="M6.6 10.8a15.1 15.1 0 0 0 6.6 6.6l2.2-2.2c.3-.3.7-.4 1-.2 1.1.4 2.3.6 3.6.6.6 0 1 .4 1 1V20c0 .6-.4 1-1 1A17 17 0 0 1 3 4c0-.6.4-1 1-1h3.5c.6 0 1 .4 1 1 0 1.3.2 2.5.6 3.6.1.3 0 .7-.2 1l-2.3 2.2z"/></svg>
      </li>
      <li>412 E. Carver Avenue,<br>Ste 2207, Tampa, FL. 33917
        <svg viewBox="0 0 24 24" aria-hidden="true"><path d="M12 2a7 7 0 0 0-7 7c0 5.2 7 13 7 13s7-7.8 7-13a7 7 0 0 0-7-7zm0 9.5A2.5 2.5 0 1 1 12 6.5a2.5 2.5 0 0 1 0 5z"/></svg>
      </li>
    </ul>

    <p class="tagline">If it chills the cooler or<br>lifts the crowd...count us in!</p>
  </section>
</main>
</body>
</html>
```